Pinecrest Harbor Foundation Web Design

The design we need is for a WordPress blog that will be our content platform. We are a registered 501(c)3 non-profit that focuses on financially supporting the treatment of cancer patients that have been told they have no hope and there is nothing the conventional medical system can do for them. Through this wesbite we want to both rasie awareness about the treatment options plus, raise funds for treating patients. The two primary target audiences of the site are...

1. Terminally ill patients and their families to let them know that there is an option other then hospice and that we are hear to support that option.

2. People looking to help donate to a worthwhile cause that resonates with them.

The website is https://pinecrestharborfoundation.org/

See attached logo designs!!!

Target Market(s)

Cancer patients and their families

Industry/Entity Type

Foundation

Font styles to use
Sans Serif

Colors
ffffff
fbed22

Requirements
Must have
• I like this look of this site. It is clean, simple, helpful, soft. I like the flow of the pages.
• http://www.meadowsforcalm.org/
• I like the design and flow but NOT the color or boldness
• https://tvbn-youth.org/
• I like this style for a donation page.
• https://www.tumorstudyhub.org/we-are-tsh/join-the-cause/donations/one-time-donation
• with the addition of a Would you like your employer to match? button.
Nice to have
• White black and gold - but soft
• Even possibly grayscale like the site I like.

```html
<!DOCTYPE html>
<html lang="en">
<head>
<meta charset="utf-8">
<title>Pinecrest Harbor Foundation</title>
<link href="https://fonts.googleapis.com/css2?family=Open+Sans:wdth,wght@75..100,300..800&display=swap" rel="stylesheet">
<style>
:root{
  --teal:#17a4a7;
  --teal-dark:#0f7f84;
  --teal-light:#4cc3c6;
  --orange:#f57c0a;
  --blue:#1565b8;
  --red:#d9443a;
  --ink:#222;
  --muted:#777;
  --footer-bg:#eef0f2;
  --white:#fff;
}
*{margin:0;padding:0;box-sizing:border-box}
html,body{width:1200px;height:2651px;overflow:hidden}
body{font-family:"Open Sans",Arial,sans-serif;color:var(--ink);background:var(--white);position:relative}
.abs{position:absolute}
/* wordmark */
.wordmark{position:absolute;display:flex;align-items:center;gap:10px;font-size:21px;font-weight:600;color:var(--ink);white-space:nowrap}
.wordmark .dot{width:14px;height:14px;border-radius:50%;background:var(--teal);flex:none}
/* header */
.site-header{position:absolute;left:0;top:0;width:1200px;height:112px;background:var(--white)}
.site-header .wordmark{left:90px;top:40px}
.contact-item{position:absolute;top:26px;display:flex;align-items:center;gap:14px}
.contact-item .ring{width:52px;height:52px;border:2px solid #ccc;border-radius:50%;display:flex;align-items:center;justify-content:center;flex:none}
.contact-item .label{color:var(--blue);font-size:17px;line-height:1.3}
.contact-item .value{font-size:13px;color:#333}
.btn-donate{position:absolute;background:var(--orange);color:var(--white);border-radius:20px;font-size:15px;text-align:center}
.site-header .btn-donate{left:975px;top:36px;width:136px;height:34px;line-height:34px}
/* nav */
.main-nav{position:absolute;left:0;top:112px;width:1200px;height:50px;background:linear-gradient(var(--teal-light),var(--teal));display:flex;padding-left:90px}
.main-nav a{color:var(--white);text-decoration:none;font-size:17px;height:50px;line-height:50px;text-align:center}
.main-nav a.active{background:var(--teal-dark)}
/* hero */
.hero{position:absolute;left:0;top:162px;width:1200px;height:556px;background:linear-gradient(90deg,#6f7376 0%,#9a9ea1 35%,#8d9194 60%,#b8bcbf 100%)}
.hero-photo{position:absolute;right:0;top:0;width:450px;height:556px;background:linear-gradient(160deg,#b7b1ab,#7b4a55 70%,#5e3a45)}
.hero h1{position:absolute;left:95px;top:206px;color:var(--white);font-size:45px;font-weight:600;font-stretch:78%;letter-spacing:.3px;white-space:nowrap}
.hero p{position:absolute;left:97px;top:270px;color:var(--white);font-size:27px;line-height:39px;width:640px}
.hero-arrows{position:absolute;left:98px;top:374px;display:flex;gap:4px}
.hero-arrows span{width:22px;height:22px;border-radius:50%;background:#555;display:flex;align-items:center;justify-content:center}
/* welcome */
.welcome h2{position:absolute;left:0;top:786px;width:1200px;text-align:center;font-size:32px;font-weight:400}
.welcome .intro{position:absolute;left:162px;top:846px;width:876px;text-align:center;font-size:13.5px;line-height:27px;color:var(--muted)}
.feature{position:absolute;top:978px;width:300px;text-align:center}
.feature .icon{width:104px;height:104px;border-radius:50%;margin:0 auto;display:flex;align-items:center;justify-content:center;box-shadow:0 4px 8px rgba(0,0,0,.2)}
.feature h3{font-size:23px;font-weight:400;margin-top:18px}
.feature p{font-size:12.5px;line-height:23px;color:var(--muted);margin:6px auto 0;width:270px}
.feature .more{font-size:12.5px;margin-top:4px;color:#333}
/* what we do */
.what{position:absolute;left:0;top:1308px;width:1200px;height:484px;background:linear-gradient(#4a4a4a,#2e2e2e)}
.what-card{position:absolute;left:148px;top:89px;width:898px;height:325px;background:var(--white)}
.what-card h2{position:absolute;left:38px;top:52px;font-size:31px;font-weight:400}
.what-card p{position:absolute;left:40px;top:108px;width:428px;font-size:13.5px;line-height:22px;color:#333;text-align:justify}
.btn-read{position:absolute;left:40px;top:236px;width:110px;height:34px;line-height:34px;border-radius:17px;background:var(--teal);color:var(--white);font-size:12px;text-align:center}
.what-video{position:absolute;right:0;top:0;width:391px;height:325px;background:linear-gradient(120deg,#d9d3ce,#e6c9c9 45%,#b9a9a4)}
/* blog */
.blog h2{position:absolute;left:0;top:1880px;width:1200px;text-align:center;font-size:31px;font-weight:400}
.post{position:absolute;top:1966px;width:320px}
.post .thumb{position:relative;height:196px;border:1px solid #ccc;padding:3px}
.post .thumb .img{width:100%;height:100%}
.post .date{position:absolute;left:3px;top:52px;width:52px;text-align:center;color:var(--white)}
.post .date .dm{background:var(--teal);height:52px;padding-top:5px;font-size:20px;line-height:22px}
.post .date .dm small{display:block;font-size:11px}
.post .date .yr{background:#222;height:48px;line-height:48px;font-size:15px}
.post h3{font-size:16.5px;font-weight:400;margin-top:14px}
.post p{font-size:12.5px;line-height:22px;color:var(--muted);margin-top:6px}
.post .read{font-size:12px;color:var(--blue);margin-top:8px}
/* footer */
.site-footer{position:absolute;left:0;top:2343px;width:1200px;height:308px;background:var(--footer-bg)}
.site-footer .wordmark{left:97px;top:78px}
.social{position:absolute;left:96px;top:146px;display:flex;gap:12px}
.social span{width:32px;height:32px;border-radius:50%;background:var(--white);box-shadow:0 1px 4px rgba(0,0,0,.3);display:flex;align-items:center;justify-content:center}
.footer-col h4{font-size:15px;font-weight:400;color:#333;margin-bottom:20px}
.footer-col{position:absolute;top:54px}
.footer-col .row{display:flex;gap:12px;font-size:13px;line-height:21px;color:#444;margin-bottom:12px}
.footer-col .row svg{flex:none;margin-top:3px}
.footer-col p{font-size:13px;line-height:21px;color:#444;width:270px}
.site-footer .btn-donate{position:relative;display:block;width:136px;height:34px;line-height:34px;margin-top:18px}
.footer-rule{position:absolute;left:90px;top:249px;width:1025px;height:1px;background:#d3d6d9}
.copyright{position:absolute;left:0;top:268px;width:1200px;text-align:center;font-size:12px;color:#333}
</style>
</head>
<body>

<header class="site-header">
  <div class="wordmark"><span class="dot"></span>Pinecrest Harbor Foundation</div>
  <div class="contact-item" style="left:522px">
    <div class="ring"><svg width="20" height="20" viewBox="0 0 24 24"><path fill="#1565b8" d="M6.6 10.8a15 15 0 0 0 6.6 6.6l2.2-2.2a1 1 0 0 1 1-.25 11 11 0 0 0 3.6.6 1 1 0 0 1 1 1V20a1 1 0 0 1-1 1A17 17 0 0 1 3 4a1 1 0 0 1 1-1h3.5a1 1 0 0 1 1 1c0 1.25.2 2.45.57 3.57a1 1 0 0 1-.25 1z"/></svg></div>
    <div><div class="label">Phone</div><div class="value">+32 (0)2 555 0187</div></div>
  </div>
  <div class="contact-item" style="left:738px">
    <div class="ring"><svg width="22" height="16" viewBox="0 0 22 16"><rect width="22" height="16" rx="2" fill="#1565b8"/><path d="M1 2l10 7 10-7" stroke="#fff" stroke-width="1.6" fill="none"/></svg></div>
    <div><div class="label">Email</div><div class="value">info@pinecrest.org</div></div>
  </div>
  <div class="btn-donate">Donate Now</div>
</header>

<nav class="main-nav">
  <a class="active" style="width:109px">Home</a>
  <a style="width:150px">About us</a>
  <a style="width:160px">Services</a>
  <a style="width:124px">Blog</a>
  <a style="width:160px">Support</a>
  <a style="width:126px">Faq</a>
  <a style="width:150px">Contact Us</a>
</nav>

<section class="hero">
  <div class="hero-photo" role="img" aria-label="Smiling woman in a scarf, a patient supported by the foundation"></div>
  <h1>PINECREST HARBOR FOUNDATION</h1>
  <p>Non-profit that focuses on financially supporting the treatment of cancer patients</p>
  <div class="hero-arrows">
    <span><svg width="8" height="10" viewBox="0 0 8 10"><path d="M6 1L2 5l4 4" stroke="#fff" stroke-width="2" fill="none"/></svg></span>
    <span><svg width="8" height="10" viewBox="0 0 8 10"><path d="M2 1l4 4-4 4" stroke="#fff" stroke-width="2" fill="none"/></svg></span>
  </div>
</section>

<section class="welcome">
  <h2>Welcome To Pinecrest Harbor Foundation</h2>
  <p class="intro">It is a long established fact that a reader will be distracted by the readable content of a page when looking at its layout. The point of using Lorem Ipsum is that it has a more-or-less normal distribution of letters, as opposed to using 'Content here, content here', making it look like readable English. Many desktop publishing packages</p>

  <div class="feature" style="left:131px">
    <div class="icon" style="background:var(--blue)"><svg width="40" height="34" viewBox="0 0 40 34" fill="#fff"><circle cx="20" cy="8" r="6"/><circle cx="8" cy="11" r="4.5"/><circle cx="32" cy="11" r="4.5"/><path d="M10 30c0-7 4-12 10-12s10 5 10 12z"/><path d="M0 28c0-5 3-9 8-9 2 0 3 .5 4 1-2 2-3 5-3 8z"/><path d="M40 28c0-5-3-9-8-9-2 0-3 .5-4 1 2 2 3 5 3 8z"/></svg></div>
    <h3>Dolorem Ipsum</h3>
    <p>It is a long established fact that a reader will be distracted by the readable</p>
    <div class="more">Learn More -&gt;</div>
  </div>
  <div class="feature" style="left:450px">
    <div class="icon" style="background:var(--orange)"><svg width="36" height="36" viewBox="0 0 36 36"><rect x="3" y="7" width="24" height="24" rx="3" stroke="#fff" stroke-width="3" fill="none"/><path d="M14 22l2-6 13-13 4 4-13 13z" fill="#fff"/></svg></div>
    <h3>Neque porro</h3>
    <p>It is a long established fact that a reader will be distracted by the readable</p>
    <div class="more">Learn More -&gt;</div>
  </div>
  <div class="feature" style="left:773px">
    <div class="icon" style="background:var(--teal)"><svg width="38" height="36" viewBox="0 0 38 36" fill="#fff"><path d="M19 0l19 9H0z"/><rect x="2" y="11" width="34" height="3"/><rect x="5" y="15" width="4" height="13"/><rect x="13" y="15" width="4" height="13"/><rect x="21" y="15" width="4" height="13"/><rect x="29" y="15" width="4" height="13"/><rect x="0" y="30" width="38" height="5"/></svg></div>
    <h3>Ipsum quia</h3>
    <p>It is a long established fact that a reader will be distracted by the readable content</p>
    <div class="more">Learn More -&gt;</div>
  </div>
</section>

<section class="what" role="img" aria-label="Dimmed photo of a group of supporters">
  <div class="what-card">
    <h2>What we do</h2>
    <p>It is a long established fact that a reader will be distracted by the readable content of a page when looking at its layout. The point of using Lorem Ipsum is that it has a more-or-less normal distribution of letters, as opposed to using 'Content here, content here', making it look like readable English. Many</p>
    <div class="btn-read">READ MORE</div>
    <div class="what-video" role="img" aria-label="Video still of two women in conversation about care">
      <svg class="abs" style="left:164px;top:128px" width="64" height="64" viewBox="0 0 64 64"><circle cx="32" cy="32" r="32" fill="#222" fill-opacity=".85"/><path d="M25 19l21 13-21 13z" fill="#fff"/></svg>
    </div>
  </div>
</section>

<section class="blog">
  <h2>Latest Blog &amp; News</h2>
  <article class="post" style="left:90px">
    <div class="thumb"><div class="img" role="img" aria-label="Counselor talking with a patient" style="background:linear-gradient(120deg,#6b5a50,#e8b89a 55%,#d6d0cc)"></div>
      <div class="date"><div class="dm">02<small>JUN</small></div><div class="yr">2017</div></div></div>
    <h3>Porro quisquam est</h3>
    <p>It has survived not only five centuries, but also the leap into electronic typesetting,</p>
    <div class="read">Read More »</div>
  </article>
  <article class="post" style="left:443px">
    <div class="thumb"><div class="img" role="img" aria-label="Group of women holding an awareness ribbon" style="background:linear-gradient(180deg,#cfe3ef,#f0b8c8 50%,#e7d5cf)"></div>
      <div class="date"><div class="dm">02<small>JUN</small></div><div class="yr">2017</div></div></div>
    <h3>Dolorem ipsum quia</h3>
    <p>It has survived not only five centuries, but also the leap into electronic typesetting, remaining</p>
    <div class="read">Read More »</div>
  </article>
  <article class="post" style="left:797px">
    <div class="thumb"><div class="img" role="img" aria-label="Woman in pink holding an awareness ribbon" style="background:linear-gradient(120deg,#e48ab8,#f3b6cf 60%,#e07aa8)"></div>
      <div class="date"><div class="dm">02<small>JUN</small></div><div class="yr">2017</div></div></div>
    <h3>Neque porro quisquam</h3>
    <p>It has survived not only five centuries, but also the leap into electronic typesetting, remaining</p>
    <div class="read">Read More »</div>
  </article>
</section>

<footer class="site-footer">
  <div class="wordmark"><span class="dot"></span>Pinecrest Harbor Foundation</div>
  <div class="social" aria-label="Share links">
    <span><svg width="12" height="12" viewBox="0 0 12 12"><path d="M3 9l6-6M4 3h5v5" stroke="#1565b8" stroke-width="1.6" fill="none"/></svg></span>
    <span><svg width="12" height="12" viewBox="0 0 12 12"><path d="M3 9l6-6M4 3h5v5" stroke="#17a4a7" stroke-width="1.6" fill="none"/></svg></span>
    <span><svg width="12" height="12" viewBox="0 0 12 12"><path d="M3 9l6-6M4 3h5v5" stroke="#d9443a" stroke-width="1.6" fill="none"/></svg></span>
    <span><svg width="12" height="12" viewBox="0 0 12 12"><path d="M3 9l6-6M4 3h5v5" stroke="#1565b8" stroke-width="1.6" fill="none"/></svg></span>
    <span><svg width="12" height="12" viewBox="0 0 12 12"><path d="M3 9l6-6M4 3h5v5" stroke="#d9443a" stroke-width="1.6" fill="none"/></svg></span>
  </div>
  <div class="footer-col" style="left:486px">
    <h4>CONTACT US</h4>
    <div class="row"><svg width="12" height="16" viewBox="0 0 12 16"><path d="M6 0a6 6 0 0 0-6 6c0 4.5 6 10 6 10s6-5.5 6-10a6 6 0 0 0-6-6z" fill="#1565b8"/><circle cx="6" cy="6" r="2.2" fill="#eef0f2"/></svg><span>2400 Alder Lane, Suite 210<br>Portland, OR 97201</span></div>
    <div class="row"><svg width="12" height="12" viewBox="0 0 24 24"><path fill="#1565b8" d="M6.6 10.8a15 15 0 0 0 6.6 6.6l2.2-2.2a1 1 0 0 1 1-.25 11 11 0 0 0 3.6.6 1 1 0 0 1 1 1V20a1 1 0 0 1-1 1A17 17 0 0 1 3 4a1 1 0 0 1 1-1h3.5a1 1 0 0 1 1 1c0 1.25.2 2.45.57 3.57a1 1 0 0 1-.25 1z"/></svg><span>503.555.0142</span></div>
    <div class="row"><svg width="13" height="10" viewBox="0 0 22 16"><rect width="22" height="16" rx="2" fill="#1565b8"/><path d="M1 2l10 7 10-7" stroke="#eef0f2" stroke-width="2" fill="none"/></svg><span>info@pinecrest.org</span></div>
  </div>
  <div class="footer-col" style="left:850px">
    <h4>DONATE</h4>
    <p>It is a long established fact that a reader will be distracted by the readable content</p>
    <div class="btn-donate">Donate Now</div>
  </div>
  <div class="footer-rule"></div>
  <div class="copyright">Copyright © 2017. All Rights Reserved</div>
</footer>

</body>
</html>
```